KRV Boltmaster Manufacturer New Web Design

We need a new theme designed for metal fastener manufacturing company, KRV Boltmaster Group, a $60M division of Marrowfield Forge Holdings, Inc. We manufacture screw, pins and washers to industrial customers (non-Automotive) such as HN Homeware, Paul Brenner, LUX, Venmora, etc. Our current website is www.boltmaster.example. We would like to stick with the same logo/color scheme, however, I'm aiming to modernize the website's look and feel.

Here are some of our competitor's websites:
- https://www.torvalink.example/
- http://glenrivet.example/
- http://www.harlowbuiltjoining.example/
- http://lugsandcustoms.example/
- http://www.dunmerebolt.example/

Target Market(s)

We primarily want to target engineers working in the following markets:
- Appliance (HN Homeware, Frostavel)
- Ag (Brenner, LUX)
- Recreational Vehicle (Venmora, Tundra Fox)
- Outdoor Power (Brellvik, Pask)

We secondarily want to target buyers working at the above markets as well as buyers at Fastener distributors such as Boltique, Parts Dynamics, Kessel Fordham.

Industry/Entity Type

Metal Forging

Number of Pages Required

1 page

Requirements
Must have
• For products: "Threaded" product as the primary focus. "Pins" product is the secondary focus, followed by all others.
• Please use same logo and color scheme as I do not plan to change.
Nice to have
• Highlight our featured proprietary products (pamphlets attached). KRV Boltmaster's GRIP-N, KelDrive, Boltmaster Coil, Avalanche.

```html
<!DOCTYPE html>
<html lang="en">
<head>
<meta charset="utf-8">
<title>KRV Boltmaster Group</title>
<link rel="stylesheet" href="https://fonts.googleapis.com/css2?family=Lexend:wght@400;500;600;700&family=Lato:ital,wght@0,400;0,700;1,400&display=swap">
<style>
:root{
  --cyan:#03a9d9;
  --navy:#0b2536;
  --navy-2:#10303f;
  --teal:#27b3c9;
  --ink:#1b2a33;
  --muted:#8a9297;
  --light:#f4f4f4;
  --line:#d6d9db;
  --white:#ffffff;
}
*{box-sizing:border-box;margin:0;padding:0}
html,body{width:1200px;height:2795px;overflow:hidden}
body{position:relative;font-family:"Lato",sans-serif;color:var(--ink);background:var(--white)}
.abs{position:absolute}

/* top bar */
.topbar{left:0;top:0;width:1200px;height:52px;background:var(--cyan);color:var(--white);font-size:14px}
.topbar span{position:absolute;top:17px;display:flex;align-items:center;gap:8px}
.topbar u{text-underline-offset:3px}

/* header */
.header{left:0;top:52px;width:1200px;height:130px;background:var(--navy);z-index:2}
.brand{position:absolute;left:78px;top:18px;display:flex;align-items:center;gap:14px}
.brand-dot{width:58px;height:58px;border-radius:50%;background:var(--white)}
.brand-name{font-family:"Lato",sans-serif;font-weight:700;font-size:30px;color:var(--teal)}
.contact-chip{position:absolute;top:30px;display:flex;align-items:center;gap:14px;color:var(--white)}
.ring{width:42px;height:42px;border-radius:50%;border:2px solid var(--teal);display:flex;align-items:center;justify-content:center}
.chip-label{font-size:15px;color:var(--teal);font-weight:700}
.chip-value{font-size:17px;font-weight:700}
.chip-sub{font-size:11px;font-style:italic;color:#c7d0d5}

.nav{left:78px;top:156px;width:1044px;height:52px;background:var(--white);display:flex;box-shadow:0 3px 8px rgba(0,0,0,.25);z-index:5}
.nav a{font-size:14px;color:#6b7378;text-decoration:none;display:flex;align-items:center;padding:0 28px;border-right:1px solid #e3e3e3;letter-spacing:.4px;white-space:nowrap}
.nav a.active{color:var(--ink);border-bottom:3px solid var(--navy)}

/* hero */
.hero{left:0;top:182px;width:1200px;height:522px;background:linear-gradient(100deg,#c9c6bb 0%,#e4e1d6 35%,#efe9d7 60%,#e8d8b0 100%);z-index:1}
.hero-title{right:78px;top:382px;text-align:right;font-family:"Lexend",sans-serif;font-weight:700;font-size:42px;line-height:47px;color:var(--navy);z-index:3}
.hero-sub{right:78px;top:490px;font-size:26px;color:var(--navy);z-index:3}

/* about */
.about{left:0;top:704px;width:1200px;height:280px;background:var(--light)}
.about h2{position:absolute;left:78px;top:62px;font-family:"Lexend",sans-serif;font-weight:500;font-size:30px;width:520px;line-height:32px}
.about h2 small{font-family:"Lato",sans-serif;font-size:20px;color:var(--muted);font-weight:400}
.about p{position:absolute;left:78px;top:150px;width:500px;font-size:14px;line-height:21px;color:var(--muted)}
.feature-box{position:absolute;top:80px;width:239px;height:138px;border:1px solid var(--line);background:var(--light);display:flex;flex-direction:column;align-items:center;justify-content:flex-end;padding-bottom:28px;font-family:"Lexend",sans-serif;font-size:17px;font-weight:500;gap:16px}
.feature-box.active{border-top:4px solid var(--navy)}

/* products */
.section-title{position:absolute;left:0;width:1200px;text-align:center;font-family:"Lexend",sans-serif;font-weight:500;font-size:36px;color:var(--navy)}
.filters{left:0;top:1090px;width:1200px;text-align:center;font-size:15px;color:var(--muted);word-spacing:4px}
.filters i{font-style:normal;margin:0 20px}
.product{position:absolute;top:1133px;width:254px}
.product-photo{width:254px;height:147px}
.product-name{text-align:center;font-family:"Lexend",sans-serif;font-weight:500;font-size:22px;margin-top:16px;color:var(--navy)}

/* cta */
.cta{left:0;top:1373px;width:1200px;height:130px;background:var(--navy);color:var(--white)}
.cta h3{position:absolute;left:78px;top:32px;font-family:"Lexend",sans-serif;font-weight:500;font-size:36px}
.cta p{position:absolute;left:78px;top:82px;font-size:16px;letter-spacing:.8px}
.btn{position:absolute;height:52px;border-radius:26px;display:flex;align-items:center;justify-content:center;font-size:19px;font-family:"Lato",sans-serif}
.btn-solid{background:var(--white);color:var(--navy)}
.btn-ghost{border:2px solid var(--white);color:var(--white)}

/* news */
.news-photo{position:absolute}
.news-date{position:absolute;font-size:12px;color:var(--muted)}
.news-title{position:absolute;font-size:15px;font-weight:700;line-height:21px;color:#111}
.news-title.side{font-weight:400;font-size:16px;letter-spacing:.6px}

/* testimonial */
.quote{left:0;top:1932px;width:1200px;height:261px;background:radial-gradient(ellipse at center,#3b3b3b 0%,#1d1d1d 55%,#0d0d0d 100%)}
.quote-mark{position:absolute;left:568px;top:42px;width:64px;height:64px;border-radius:50%;border:2px solid var(--teal);color:var(--teal);font-family:"Lexend",sans-serif;font-size:40px;display:flex;align-items:center;justify-content:center}
.quote p{position:absolute;left:220px;top:122px;width:760px;text-align:center;font-style:italic;font-size:15px;line-height:22px;color:#b5b8ba}
.quote .who{position:absolute;left:0;top:182px;width:1200px;text-align:center;color:var(--white);font-size:14px}
.quote .who b{color:var(--teal);font-family:"Lexend",sans-serif;font-size:21px;font-weight:500}

/* newsletter */
.newsletter h3{position:absolute;left:78px;top:2237px;font-family:"Lexend",sans-serif;font-weight:500;font-size:38px;color:var(--navy)}
.newsletter p{position:absolute;left:78px;top:2295px;font-size:15px;color:var(--muted)}
.field{position:absolute;border:1px solid var(--line);border-radius:26px;background:var(--white);color:var(--muted);font-size:13px;display:flex;align-items:center;padding-left:24px}

/* footer */
.footer{left:0;top:2420px;width:1200px;height:313px;background:linear-gradient(180deg,#3a3a3a 0%,#2a2a2a 60%,#1e1e1e 100%)}
.card{left:78px;top:2357px;width:332px;height:332px;background:rgba(240,240,240,.93)}
.card-head{position:absolute;left:0;top:0;width:332px;height:60px;background:var(--navy);color:var(--white);font-family:"Lexend",sans-serif;font-weight:500;font-size:20px;padding:18px 0 0 44px}
.dots{position:absolute;right:30px;top:25px;display:flex;gap:6px}
.dots i{width:10px;height:10px;border-radius:50%;border:1.5px solid var(--white)}
.dots i.on{background:var(--white)}
.card-brand{position:absolute;left:44px;top:92px;display:flex;align-items:center;gap:12px}
.card-brand .brand-dot{width:44px;height:44px;background:var(--navy)}
.card-brand .brand-name{font-size:23px;color:var(--teal)}
.card-row{position:absolute;left:44px;display:flex;gap:18px;font-size:14px;line-height:22px;color:#333}
.footer-title{position:absolute;font-family:"Lexend",sans-serif;font-weight:500;font-size:20px;color:var(--white)}
.ghost-field{position:absolute;border:1.5px solid var(--white);border-radius:22px;color:var(--white);font-size:12px;padding:12px 0 0 12px}
.footer p{position:absolute;left:860px;top:70px;width:260px;font-size:14px;line-height:22px;color:#e3e3e3}

.bottombar{left:0;top:2733px;width:1200px;height:62px;background:var(--navy-2);color:var(--white);text-align:center;font-family:"Lexend",sans-serif;font-size:14px;font-weight:500;padding-top:22px}
.bottombar b{color:var(--teal);font-weight:500}
</style>
</head>
<body>

<div class="abs topbar">
  <span style="left:78px"><svg width="14" height="14" viewBox="0 0 14 14"><path d="M1 6h7L5 3M8 6 5 9" stroke="#fff" stroke-width="2" fill="none"/><path d="M8 1h5v12H8" stroke="#fff" stroke-width="2" fill="none"/></svg>SIGN-IN</span>
  <span style="left:180px"><svg width="16" height="12" viewBox="0 0 16 12"><rect x="1" y="1" width="14" height="10" fill="none" stroke="#fff" stroke-width="1.5"/><path d="M1 1l7 6 7-6" stroke="#fff" stroke-width="1.5" fill="none"/></svg>hello@northpinedesk.example</span>
  <span style="left:886px">Contact Us &nbsp;&nbsp;/&nbsp;&nbsp; <u>Request A Quote</u></span>
</div>

<header class="abs header">
  <div class="brand"><div class="brand-dot"></div><div class="brand-name">KRV Boltmaster Group</div></div>
  <div class="contact-chip" style="left:680px">
    <div class="ring"><svg width="18" height="18" viewBox="0 0 24 24"><path d="M6.6 10.8a15 15 0 0 0 6.6 6.6l2.2-2.2a1 1 0 0 1 1-.25 11 11 0 0 0 3.6.6 1 1 0 0 1 1 1V20a1 1 0 0 1-1 1A17 17 0 0 1 3 4a1 1 0 0 1 1-1h3.5a1 1 0 0 1 1 1c0 1.25.2 2.45.6 3.6a1 1 0 0 1-.25 1z" fill="#27b3c9"/></svg></div>
    <div><div class="chip-label">Call Today:</div><div class="chip-value">555-014-7720</div></div>
  </div>
  <div class="contact-chip" style="left:880px">
    <div class="ring"><svg width="18" height="18" viewBox="0 0 20 20"><circle cx="8" cy="8" r="5.5" stroke="#27b3c9" stroke-width="2.2" fill="none"/><path d="M12 12l5 5" stroke="#27b3c9" stroke-width="2.4"/></svg></div>
    <div><div class="chip-label">Search</div><div class="chip-sub">Search here...</div></div>
  </div>
</header>

<section class="abs hero" role="img" aria-label="Close-up photograph of metal lock washers and stamped parts"></section>

<nav class="abs nav">
  <a class="active">HOME</a><a>PRODUCTS</a><a>CAPABILITIES</a><a>ENGINEERING</a><a>QUALITY</a><a>ABOUT US</a><a style="border-right:none">CONTACT/QUOTE REQUEST</a>
</nav>

<div class="abs hero-title">BETTER FASTENERS FOR<br>BETTER PRODUCTS</div>
<div class="abs hero-sub">Simple Ideas Help The Industry Take Off...</div>

<section class="abs about">
  <h2>We Are KRV Boltmaster - <small>Leading provider of industrial products near you.</small></h2>
  <p>Known as KRV Boltmaster Group today, the company is the result of a 2010 merger of KRV businesses that have a long, rich history in the industrial hardware market. This history dates back to the 1920s, when two of KRV Boltmaster Group's main product lines were created.</p>
  <div class="feature-box active" style="left:633px">
    <svg width="62" height="50" viewBox="0 0 62 50"><path d="M4 48V24l14 8V24l14 8V24l14 8V6h8v42z" fill="#c4c8cb"/><rect x="46" y="2" width="8" height="4" fill="#c4c8cb"/></svg>
    Our Services
  </div>
  <div class="feature-box" style="left:883px">
    <svg width="56" height="50" viewBox="0 0 56 50"><circle cx="22" cy="26" r="11" fill="none" stroke="#0b2536" stroke-width="5" stroke-dasharray="4 3"/><circle cx="22" cy="26" r="5" fill="#27b3c9"/><circle cx="42" cy="12" r="7" fill="none" stroke="#0b2536" stroke-width="4" stroke-dasharray="3 2.5"/><circle cx="42" cy="38" r="7" fill="none" stroke="#27b3c9" stroke-width="4" stroke-dasharray="3 2.5"/></svg>
    Our Products
  </div>
</section>

<h2 class="section-title" style="top:1034px">Our Products</h2>
<div class="abs filters">All<i>/</i>Lock washers<i>/</i>Pins<i>/</i>Stampings<i>/</i>Threaded</div>
<div class="product" style="left:78px"><div class="product-photo" role="img" aria-label="Photograph of assorted lock washers" style="background:linear-gradient(135deg,#9da3a6,#d7dadb 50%,#8e9497)"></div><div class="product-name">LOCK WASHERS</div></div>
<div class="product" style="left:342px"><div class="product-photo" role="img" aria-label="Photograph of hitch and clevis pins" style="background:linear-gradient(135deg,#cfd1d1,#b3a77a 50%,#4a4a48)"></div><div class="product-name">PINS</div></div>
<div class="product" style="left:605px"><div class="product-photo" role="img" aria-label="Photograph of stamped metal parts" style="background:linear-gradient(135deg,#b9bcbd,#6f7476 50%,#c8cacb)"></div><div class="product-name">STAMPINGS</div></div>
<div class="product" style="left:868px"><div class="product-photo" role="img" aria-label="Photograph of threaded bolts and screws" style="background:linear-gradient(135deg,#c6c8c9,#5e5a4e 50%,#a9acae)"></div><div class="product-name">THREADED</div></div>

<section class="abs cta">
  <h3>Factory consulation For Free</h3>
  <p>Bolts theme for all your factory products and engineering services.</p>
  <div class="btn btn-solid" style="left:705px;top:39px;width:230px">Get Consultation</div>
  <div class="btn btn-ghost" style="left:948px;top:39px;width:174px">Join Us Now</div>
</section>

<h2 class="section-title" style="top:1553px">Latest News</h2>
<div class="news-photo" role="img" aria-label="Photograph of an underground mine tunnel" style="left:78px;top:1619px;width:321px;height:164px;background:linear-gradient(135deg,#3a2a1a,#8a5a2a 50%,#2a1e12)"></div>
<div class="news-date" style="left:80px;top:1796px">August 8, 2011</div>
<div class="news-title" style="left:80px;top:1824px">KRV Integrates Leading Midwest<br>Fastener Divisions</div>
<div class="news-photo" role="img" aria-label="Photograph of a business meeting around a conference table" style="left:451px;top:1619px;width:321px;height:164px;background:linear-gradient(135deg,#dfe6ee,#7d8ea0 50%,#eef2f6)"></div>
<div class="news-date" style="left:455px;top:1796px">August 8, 2011</div>
<div class="news-title" style="left:455px;top:1824px">KRV Integrates Leading Midwest<br>Fastener Divisions</div>
<div class="news-photo" role="img" aria-label="Photograph of engineers beside large gears" style="left:794px;top:1619px;width:126px;height:119px;background:linear-gradient(135deg,#4c5a66,#9aa4ab 50%,#2f3a44)"></div>
<div class="news-date" style="left:938px;top:1634px">August 8, 2011</div>
<div class="news-title side" style="left:938px;top:1660px">KRV Integrates<br>Leading Midwest<br>Fastener Divisions</div>
<div class="news-photo" role="img" aria-label="Photograph of railway tracks" style="left:794px;top:1759px;width:126px;height:119px;background:linear-gradient(135deg,#6e7f8e,#3e4a52 50%,#9b8f7e)"></div>
<div class="news-date" style="left:938px;top:1775px">August 8, 2011</div>
<div class="news-title side" style="left:938px;top:1800px">KRV Integrates<br>Leading Midwest<br>Fastener Divisions</div>

<section class="abs quote" role="img" aria-label="Background photograph of a factory hall">
  <div class="quote-mark">&ldquo;</div>
  <p>"Lorem Ipsum is simply dummy text of the printing and typesetting industry. Lorem Ipsum has been the industry's standard dummy text ever since the 1500s, when an unknown printer took a galley."</p>
  <div class="who"><b>Lorem ipsum,</b> Head Officer at abc Company</div>
</section>

<section class="newsletter">
  <h3>Newsletter</h3>
  <p>Subscribe to Our Newsletter to Get News &amp; Updates</p>
  <div class="field" style="left:514px;top:2259px;width:406px;height:52px">Name</div>
  <div class="btn" style="left:925px;top:2259px;width:197px;background:var(--navy);color:var(--white);font-size:20px">Subscribe</div>
</section>

<footer class="abs footer" role="img" aria-label="Dark background photograph of machine gears">
  <div class="footer-title" style="left:464px;top:30px">INQUIRY FORM</div>
  <div class="ghost-field" style="left:464px;top:72px;width:176px;height:42px">Name</div>
  <div class="ghost-field" style="left:650px;top:72px;width:176px;height:42px">Company Name</div>
  <div class="ghost-field" style="left:464px;top:124px;width:176px;height:42px">Phone</div>
  <div class="ghost-field" style="left:650px;top:124px;width:176px;height:42px">E-Mail</div>
  <div class="ghost-field" style="left:464px;top:176px;width:362px;height:42px">Message</div>
  <div class="btn btn-solid" style="left:464px;top:230px;width:124px;height:42px;font-size:17px">Submit</div>
  <div class="footer-title" style="left:860px;top:30px">ASK THE EXPERT</div>
  <p>KRV Boltmaster Group always strives to improve our customer's products through designing and manufacturing value-added, quality solutions.</p>
  <div class="btn btn-solid" style="left:859px;top:178px;width:263px;height:50px;font-size:22px">Ask Us Now</div>
</footer>

<div class="abs card">
  <div class="card-head">STAMPINGS<div class="dots"><i class="on"></i><i></i><i></i><i></i></div></div>
  <div class="card-brand"><div class="brand-dot"></div><div class="brand-name">KRV Boltmaster</div></div>
  <div class="card-row" style="top:176px"><svg width="18" height="22" viewBox="0 0 18 22"><path d="M9 21s7-7 7-12A7 7 0 0 0 2 9c0 5 7 12 7 12z" fill="none" stroke="#333" stroke-width="1.6"/><circle cx="9" cy="9" r="2.5" fill="#333"/></svg><span>418 Quarry Lane<br>Halvern, ST 00412</span></div>
  <div class="card-row" style="top:232px"><svg width="18" height="18" viewBox="0 0 24 24"><path d="M6.6 10.8a15 15 0 0 0 6.6 6.6l2.2-2.2a1 1 0 0 1 1-.25 11 11 0 0 0 3.6.6 1 1 0 0 1 1 1V20a1 1 0 0 1-1 1A17 17 0 0 1 3 4a1 1 0 0 1 1-1h3.5a1 1 0 0 1 1 1c0 1.25.2 2.45.6 3.6a1 1 0 0 1-.25 1z" fill="none" stroke="#333" stroke-width="1.8"/></svg><span>555-014-7720</span></div>
  <div class="card-row" style="top:276px"><svg width="18" height="14" viewBox="0 0 18 14"><rect x="1" y="1" width="16" height="12" fill="none" stroke="#333" stroke-width="1.5"/><path d="M1 1l8 7 8-7" stroke="#333" stroke-width="1.5" fill="none"/></svg><span>sales@boltmaster.example</span></div>
</div>

<div class="abs bottombar">&copy; <b>KRV Boltmaster Group</b> - 2017. All Rights Reserved.</div>

</body>
</html>
```